Website for Torvel Capital - investment banking firm

We have a corporate identity (thanks to Ravinka/31842) and want to extend that into a website design.  See the attached zipped files.
We have software folks in-house to do the coding.
See the attached Project Brief & Notes for more details.  Don't worry about the actual text - lorem ipsum will be fine.
The server will be Apache.
Thank you!
Desmond

Industry/Entity Type
Investment

```html
<!DOCTYPE html>
<html lang="en">
<head>
<meta charset="utf-8">
<title>Torvel Capital</title>
<link rel="stylesheet" href="https://fonts.googleapis.com/css2?family=Cinzel:wght@400;600;700&family=Lato:ital,wght@0,400;0,700;1,400&family=Ubuntu:wght@400&display=swap">
<style>
:root{
  --navy:#0e3a7c;
  --navy-deep:#02336f;
  --blue:#1d4f9c;
  --blue-light:#4d8fcf;
  --dark-text:#333;
  --rule:#c9c9c9;
  --white:#fff;
}
*{box-sizing:border-box;margin:0;padding:0}
html,body{width:1200px;height:1148px;overflow:hidden;background:var(--white)}
.page{position:relative;width:1280px;height:1224px;transform:scale(.9375);transform-origin:0 0;font-family:"Lato",sans-serif;color:var(--dark-text);
  background:linear-gradient(90deg,#e4e8ec 0,#f7f8f9 30%,#f2f4f6 70%,#d8dde2 100%)}
.site-header{position:absolute;left:0;top:0;width:1280px;height:101px;background:var(--white)}
.follow{position:absolute;left:140px;top:40px;display:flex;align-items:center;gap:8px;font-family:"Cinzel",serif;font-weight:700;font-size:21px;color:var(--blue)}
.follow .dot{width:28px;height:28px;border-radius:50%;background:#6d6d6d;display:inline-block}
.brand{position:absolute;left:462px;top:22px;display:flex;align-items:center;gap:14px}
.brand .mark{width:56px;height:56px;border-radius:50%;background:var(--blue)}
.brand .name{font-family:"Cinzel",serif;font-weight:600;font-size:36px;color:var(--blue);white-space:nowrap}
.question{position:absolute;right:142px;top:28px;display:flex;gap:12px;align-items:center}
.question .label{font-family:"Cinzel",serif;font-weight:700;font-size:16px;color:var(--blue)}
.question .number{font-family:"Cinzel",serif;font-size:28px;color:#333;line-height:1}
.main-nav{position:absolute;left:0;top:101px;width:1280px;height:44px;background:linear-gradient(#234f99,#153e82)}
.main-nav ul{position:absolute;left:140px;display:flex;list-style:none;height:44px}
.main-nav li{font-family:"Cinzel",serif;font-weight:600;font-size:15px;color:var(--white);padding:0 18px;line-height:44px;border-right:1px solid #0d2c63;white-space:nowrap}
.main-nav li.active{background:linear-gradient(#5b9fd6,#2a6bb3);padding:0 24px}
.hero{position:absolute;left:140px;top:145px;width:1000px;height:550px;background:radial-gradient(ellipse at 78% 45%,#c89c8e 0,#9bb1cc 22%,#b8cce0 45%,#dbe5ef 80%)}
.hero-caption{position:absolute;left:0;top:350px;width:533px;height:159px;background:rgba(255,255,255,.82);padding:12px 18px}
.hero-caption h1{font-family:"Cinzel",serif;font-weight:700;font-size:38px;color:var(--blue);line-height:1.1;white-space:nowrap}
.hero-caption p{font-family:"Ubuntu",sans-serif;font-size:20px;color:#333;line-height:1.4;margin-top:6px;white-space:nowrap}
.content{position:absolute;left:140px;top:695px;width:1000px;height:360px;background:var(--white);box-shadow:0 2px 8px rgba(0,0,0,.2)}
.col{position:absolute;top:34px}
.col h2{font-family:"Cinzel",serif;font-weight:600;font-size:23px;color:#222;padding-bottom:8px;border-bottom:1px solid var(--rule);position:relative;white-space:nowrap}
.col h2 span{color:var(--blue)}
.col h2::after{content:"";position:absolute;left:8px;bottom:-7px;width:12px;height:12px;background:var(--white);border-right:1px solid var(--rule);border-bottom:1px solid var(--rule);transform:rotate(45deg)}
.divider{position:absolute;top:60px;width:1px;height:230px;background:linear-gradient(transparent,#ddd,transparent)}
.about-photo{margin-top:20px;width:286px;height:110px;background:linear-gradient(90deg,#b9c4cc,#d9d2c9 40%,#2b3140 60%,#c9ccd0)}
.about p{font-size:13.5px;line-height:21px;color:#333;margin-top:9px;width:290px}
.more{position:absolute;top:265px;font-size:14px;font-weight:700;color:#333;white-space:nowrap}
.services{list-style:none;margin-top:10px}
.services li{display:flex;align-items:center;height:70px;border-bottom:2px solid #e2e2e2;font-size:16px;font-weight:700;color:#444;line-height:19px}
.services li svg{flex:none;margin-right:10px}
.services li .sep{width:1px;height:28px;background:#ccc;margin-right:11px}
.quote{margin-top:14px;width:281px;height:138px;background:#e3e4e6;border-radius:8px;padding:16px 8px 12px 12px;position:relative;font-style:italic;font-size:13px;line-height:24px;color:#333;white-space:nowrap}
.quote::after{content:"";position:absolute;right:36px;bottom:-20px;border-top:20px solid #e3e4e6;border-left:30px solid transparent}
.quote .qmark{font-family:Georgia,serif;font-size:40px;color:#bbb;position:absolute;left:8px;top:6px;font-style:normal}
.client{display:flex;align-items:flex-end;gap:12px;margin-top:-12px;margin-left:12px;position:relative}
.client .avatar{width:72px;height:72px;border-radius:6px;border:3px solid var(--white);box-shadow:0 1px 4px rgba(0,0,0,.35);background:linear-gradient(#6c5a4c,#2e4a78)}
.client .who{font-size:14px;padding-bottom:14px}
.site-footer{position:absolute;left:0;top:990px;width:1280px;height:234px;background:var(--navy-deep)}
.footer-links{position:absolute;left:146px;top:1083px;font-size:14px;color:var(--white)}
.footer-links i{font-style:normal;margin:0 8px}
.newsletter{position:absolute;left:143px;top:1124px;display:flex;align-items:center}
.newsletter .icon{width:34px;height:34px;border-radius:50%;background:var(--navy-deep);border:2px solid var(--white);display:flex;align-items:center;justify-content:center;position:relative;z-index:1}
.newsletter .field{width:160px;height:36px;background:var(--white);border-radius:0 3px 3px 0;margin-left:-4px;font-size:11px;color:#999;line-height:36px;padding-left:16px}
.newsletter .btn{margin-left:4px;height:36px;padding:0 8px;background:var(--blue-light);color:var(--white);font-size:14px;line-height:36px;border-radius:3px}
.copyright{position:absolute;left:143px;top:1180px;font-size:13px;color:var(--white)}
.contact{position:absolute;left:848px;top:1078px;color:var(--white);font-size:14px;font-style:normal}
.contact .row{display:flex;gap:12px;margin-bottom:12px;line-height:17px}
.contact .row b{font-weight:700;letter-spacing:.5px}
</style>
</head>
<body>
<div class="page">
  <header class="site-header">
    <div class="follow">Follow Us :
      <span class="dot" aria-label="Social profile"></span>
      <span class="dot" aria-label="Social profile"></span>
      <span class="dot" aria-label="Social profile"></span>
    </div>
    <div class="brand"><span class="mark"></span><span class="name">TorvelCapital</span></div>
    <div class="question">
      <svg width="44" height="44" viewBox="0 0 44 44"><circle cx="22" cy="22" r="20" fill="none" stroke="#333" stroke-width="2.5"/><path d="M16 13c-2 2-2 5 0 9s6 8 10 9c2 0 3-1 4-2l-3-4-3 1c-2-1-4-4-5-6l1-3-4-4z" fill="#333"/></svg>
      <div><div class="label">Have A Question ?</div><div class="number">555-214-3870</div></div>
    </div>
  </header>

  <nav class="main-nav"><ul>
    <li class="active">Home</li><li>About</li><li>Services</li><li>Current Engagements</li><li>Completed Transactions</li><li>Contact Us</li>
  </ul></nav>

  <section class="hero" role="img" aria-label="Close-up of a hand placing a blue jigsaw puzzle piece">
    <div class="hero-caption">
      <h1>Torvel Capital LLC is</h1>
      <p>Dallas-based private investment banking<br>advisory firm that acts as an intermediary on<br>behalf of buyers &amp; sellers of private companies.</p>
    </div>
  </section>

  <footer class="site-footer"></footer>

  <main class="content">
    <div class="col about" style="left:17px;width:290px">
      <h2 style="padding-left:6px">About <span>TorvelCapital</span></h2>
      <div class="about-photo" role="img" aria-label="Business team talking around a table"></div>
      <p>Torvel Capital's history in mergers and acquisitions traces back to 1998. We pride our selves in successfully matching buyers with sellers and enabling shareholders of all.</p>
      <div class="more" style="left:206px">Read More »</div>
    </div>
    <div class="divider" style="left:323px"></div>
    <div class="col" style="left:365px;width:282px">
      <h2>What <span>We Do</span></h2>
      <ul class="services">
        <li><svg width="42" height="34" viewBox="0 0 42 34"><path d="M3 14l9-8 8 3 6-3 13 8-8 9-5 5-4-2-3 2-5-4-6-3z" fill="none" stroke="#666" stroke-width="2.5" stroke-linejoin="round"/></svg><span class="sep"></span>Buy-Side Acquisitions</li>
        <li><svg width="42" height="34" viewBox="0 0 42 34"><rect x="3" y="22" width="5" height="10" fill="#666"/><rect x="11" y="16" width="5" height="16" fill="#666"/><rect x="19" y="18" width="5" height="14" fill="#666"/><rect x="27" y="10" width="5" height="22" fill="#666"/><path d="M3 18l9-7 7 4 14-11" fill="none" stroke="#666" stroke-width="2"/><text x="14" y="10" font-size="11" font-weight="700" fill="#666">$</text></svg><span class="sep"></span>Recapitalizations &amp;<br>Growth Capital Partnerships</li>
        <li style="border:0;height:86px"><svg width="42" height="34" viewBox="0 0 42 34"><text x="12" y="14" font-size="15" font-weight="700" fill="#666">$</text><path d="M2 22h10l8 3h9l3-2v4l-10 5H2z" fill="#666"/></svg><span class="sep"></span>Sell-Side Transactions</li>
      </ul>
      <div class="more" style="left:199px">Read More »</div>
    </div>
    <div class="divider" style="left:663px"></div>
    <div class="col" style="left:702px;width:284px">
      <h2>Client <span>Testimonials</span></h2>
      <div class="quote"><span class="qmark">“</span>&nbsp;&nbsp;&nbsp;&nbsp;&nbsp;&nbsp;&nbsp;Duis autem vel eum iriureol hder in a<br>vultat velit esse moles conqat vela ilu adipsin<br>&nbsp;feugiat.Duis autem vel eum ure hendrern<br>vultat velit esse autm vel eum iriure dol</div>
      <div class="client"><div class="avatar" role="img" aria-label="Client portrait"></div><div class="who">Mr. Dolore Eu Feugiat</div></div>
      <div class="more" style="left:199px">Read More »</div>
    </div>
  </main>

  <div class="footer-links">Home<i>|</i>About<i>|</i>Services<i>|</i>Current Engagements<i>|</i>Completed Transactions<i>|</i>Contact Us</div>
  <div class="newsletter">
    <span class="icon"><svg width="18" height="13" viewBox="0 0 18 13"><rect x="1" y="1" width="16" height="11" fill="none" stroke="#fff" stroke-width="1.6"/><path d="M1 1l8 6 8-6" fill="none" stroke="#fff" stroke-width="1.6"/></svg></span>
    <span class="field">Sign Up for Newsletter</span>
    <span class="btn">SUBSCRIBE</span>
  </div>
  <div class="copyright">© Copyright 2014 Torvel Capital. | All Rights Reserved</div>

  <address class="contact">
    <div class="row"><svg width="16" height="20" viewBox="0 0 16 20"><path d="M8 1a6 6 0 0 0-6 6c0 5 6 12 6 12s6-7 6-12a6 6 0 0 0-6-6z" fill="#fff"/><circle cx="8" cy="7" r="2.3" fill="#02336f"/></svg><span>Hong Kong: Suite 1804 Harbourline Tower<br>12 - 18 Marlow Road West<br>Eastbay, Hong Kong</span></div>
    <div class="row"><svg width="18" height="16" viewBox="0 0 18 16"><path d="M3 14c0-6 4-10 9-10l3-3 2 2-3 3c-3 0-6 3-7 8z" fill="#fff"/></svg><b>555-214-3870</b></div>
    <div class="row"><svg width="17" height="12" viewBox="0 0 17 12"><rect x="1" y="1" width="15" height="10" fill="#fff"/><path d="M1 1l7.5 6L16 1" fill="none" stroke="#02336f" stroke-width="1.4"/></svg><span style="letter-spacing:.6px">info@torvelcapital.com</span></div>
  </address>
</div>
</body>
</html>
```